Business Card for Health Food Store

I need a business card for a health food store that includes the following information.

=========
FRONT
=========

***White background***

Bright Harvest (logo)
Supplements - Health Foods - Remedies

2214 Alder Rd.
Fernvale, CA 94512
(corner of Ferris Ln.)

707-482-3196

BrightHarvest.co
BrightHarvestGoods@mailbox-example.com

On the right side of the front of the card, use a circle type seal with 25 large in the middle. Put the dates below it.
"Celebrating 25 Years"
1997 - 2022

*DO NOT USE A PERSON'S NAME ON THE CARD*

==========
BACK
==========

***Green background***

Full logo in white along with the social logos and handles.

FB Logo / BrightHarvestShop
IG Logo / BrightHarvestShop
Twitter Logo / VisitBrightHarvest

When done I'll need the file in PSD and AI.

Target Market(s)

Surrounding local community

Industry/Entity Type

Retail Health Food Store

Contact Information for Business Card

See brief

Requirements
Must have
• Must be double-sided

```html
<!DOCTYPE html>
<html lang="en">
<head>
<meta charset="utf-8">
<title>Bright Harvest – Business Card</title>
<link rel="stylesheet" href="https://fonts.googleapis.com/css2?family=Arimo:wght@400;700&family=Lexend:wght@700&family=Oswald:wght@500&display=swap">
<style>
  :root {
    --bg: #c4c4c4;
    --charcoal: #2a2a2a;
    --green: #4cbb17;
    --white: #ffffff;
    --ink: #111111;
    --text-light: #e6e6e6;
  }
  * { box-sizing: border-box; margin: 0; padding: 0; }
  html, body { width: 1200px; height: 800px; overflow: hidden; }
  body {
    background: var(--bg);
    font-family: "Arimo", Arial, sans-serif;
    display: flex;
    align-items: center;
    justify-content: center;
    gap: 40px;
  }
  .card {
    position: relative;
    width: 540px;
    height: 309px;
    overflow: hidden;
    box-shadow: 0 10px 24px rgba(0,0,0,0.25);
  }

  /* ---------- Front ---------- */
  .card--front { background: var(--charcoal); }
  .front__brand-panel {
    position: absolute; top: 0; right: 0;
    width: 262px; height: 100%;
    background: var(--white);
  }
  .band {
    position: absolute; left: 0; right: 0;
    background: var(--green);
    display: flex; align-items: center;
    color: var(--white);
  }
  .front__band { top: 204px; height: 32px; justify-content: flex-end; padding-right: 22px; }
  .front__band-text { font-size: 15px; letter-spacing: 0.3px; white-space: nowrap; }

  .contact {
    position: absolute; left: 18px; top: 48px;
    width: 254px;
    color: var(--text-light);
    font-size: 11.5px; line-height: 1.3;
    white-space: nowrap;
  }
  .contact__row { display: flex; align-items: flex-start; gap: 6px; }
  .contact__row + .contact__row { margin-top: 1px; }
  .contact__group { margin-top: 22px; }
  .contact__icon { width: 12px; height: 12px; flex: none; margin-top: 1px; }

  .brand {
    position: absolute;
    display: flex; flex-direction: column; align-items: center;
  }
  .brand__name-row { display: flex; align-items: center; gap: 8px; }
  .brand__dot { border-radius: 50%; background: var(--green); flex: none; }
  .brand__name { font-family: "Lexend", "Arial Black", sans-serif; font-weight: 700; line-height: 1; white-space: nowrap; }
  .brand__tagline {
    font-family: "Oswald", "Arial Narrow", sans-serif; font-weight: 500;
    color: var(--green); text-transform: uppercase; letter-spacing: 1px;
    white-space: nowrap;
  }

  .front__brand { top: 78px; right: 0; width: 262px; }
  .front__brand .brand__dot { width: 16px; height: 16px; }
  .front__brand .brand__name { font-size: 24px; color: var(--ink); }
  .front__brand .brand__tagline { font-size: 10.5px; margin-top: 6px; letter-spacing: 0.8px; }

  /* ---------- Back ---------- */
  .card--back { background: var(--charcoal); }
  .back__brand { top: 84px; left: 0; right: 0; }
  .back__brand .brand__dot { width: 26px; height: 26px; }
  .back__brand .brand__name { font-size: 40px; color: var(--white); }
  .back__brand .brand__tagline { font-size: 14px; margin-top: 8px; }

  .back__band-social { top: 196px; height: 28px; justify-content: flex-end; padding-right: 24px; }
  .back__band-web { top: 258px; height: 28px; padding-left: 24px; }
  .social { display: flex; align-items: center; gap: 8px; font-size: 14px; white-space: nowrap; }
  .social__mark { width: 17px; height: 17px; border-radius: 50%; background: var(--white); flex: none; }
</style>
</head>
<body>

  <section class="card card--front" aria-label="Business card front">
    <div class="front__brand-panel"></div>

    <div class="brand front__brand">
      <div class="brand__name-row">
        <span class="brand__dot"></span>
        <span class="brand__name">Bright Harvest</span>
      </div>
      <span class="brand__tagline">Supplements · Health Foods · Remedies</span>
    </div>

    <div class="contact">
      <div class="contact__row">
        <svg class="contact__icon" viewBox="0 0 12 12" aria-hidden="true"><path d="M6 0.5a4 4 0 0 0-4 4c0 3 4 7 4 7s4-4 4-7a4 4 0 0 0-4-4z" fill="#4cbb17"/><circle cx="6" cy="4.5" r="1.5" fill="#2a2a2a"/></svg>
        <span>2214 Alder Rd.<br>Fernvale, CA 94512</span>
      </div>
      <div class="contact__group">
        <div class="contact__row">
          <svg class="contact__icon" viewBox="0 0 12 12" aria-hidden="true"><path d="M2.5 1h2l1 2.5-1.3 1a6 6 0 0 0 3.3 3.3l1-1.3 2.5 1v2a1 1 0 0 1-1 1A9.5 9.5 0 0 1 1.5 2a1 1 0 0 1 1-1z" fill="#4cbb17"/></svg>
          <span>707-482-3196</span>
        </div>
        <div class="contact__row">
          <svg class="contact__icon" viewBox="0 0 12 12" aria-hidden="true"><circle cx="6" cy="6" r="5" fill="none" stroke="#4cbb17" stroke-width="1.2"/><ellipse cx="6" cy="6" rx="2.2" ry="5" fill="none" stroke="#4cbb17" stroke-width="1"/><line x1="1" y1="6" x2="11" y2="6" stroke="#4cbb17" stroke-width="1"/></svg>
          <span>BrightHarvest.co</span>
        </div>
        <div class="contact__row">
          <svg class="contact__icon" viewBox="0 0 12 12" aria-hidden="true"><rect x="0.5" y="2.5" width="11" height="7.5" fill="#4cbb17"/><path d="M0.5 2.5 6 7l5.5-4.5" fill="none" stroke="#2a2a2a" stroke-width="1"/></svg>
          <span>BrightHarvestGoods@mailbox-example.com</span>
        </div>
      </div>
    </div>

    <div class="band front__band">
      <span class="front__band-text">Celebrating 25 Years: 1997 - 2022</span>
    </div>
  </section>

  <section class="card card--back" aria-label="Business card back">
    <div class="brand back__brand">
      <div class="brand__name-row">
        <span class="brand__dot"></span>
        <span class="brand__name">Bright Harvest</span>
      </div>
      <span class="brand__tagline">Supplements · Health Foods · Remedies</span>
    </div>

    <div class="band back__band-social">
      <div class="social">
        <span class="social__mark"></span>
        <span>/BrightHarvestShop</span>
      </div>
    </div>

    <div class="band back__band-web">
      <div class="social">
        <span class="social__mark"></span>
        <span>www.social-example.com/brightharvestfoods</span>
      </div>
    </div>
  </section>

</body>
</html>
```